eBook-Cover für Thriller gesucht
An dieser Stelle ein großes Lob und vielen Dank an die Designerin Larosa. Auch das zweite Buchcover ist wieder überaus gelungen, eine ganz tolle Arbeit. Auch die angenehme Zusammenarbeit war mir, wie schon beim ersten Auftrag, eine Freude. Ebenso hervorzuheben ist die Schnelligkeit und Kreativität, mit der die Designerin auf Änderungswünsche reagiert. Als Auftraggeber gebe ich verdiente fünf Sterne und bin mit dem Ergebnis wirklich sehr zufrieden.
Zielgruppe
Ich bin Autor. Zielgruppe sind (anspruchsvolle) Leser/innen von Thrillern und Kriminalromanen im ebook-Bereich.
Aufgabenstellung
- Gesucht wird ein ebook-Cover für einen Thriller mit dem Titel 'Kaltgrund'
- Grobe Aufteilung siehe Skizzen
- Fokus des Covers liegt auf dem Buchtitel und dem Motiv ('Blauer Drachen')
- Hintergrund eher hell, Assoziation mit zarter Eisfläche mit angedeuteten Rissen vom Hauptmotiv ausgehend. Dadurch auch Tiefe und Dreidimensionalität. (Beispiel zum Hintergrund: 'Schattenfrist' von Heinrich Wendel, jedoch ohne Blut )
-Titelschrift groß, Stil 'gekratzt' bzw. 'gestrichelt', (Schriftart ähnlich wie Autorenname bei 'Die Schleuse' von Matthias Kolbe). Schrift groß und 'treppenförmig' neben dem Hauptmotiv angeordnet. Schriftfarbe schwarz/dunkelblau, ähnlich Hauptmotiv (Bsp.: 'Schwarzeid' von Heinrich Wendel)
Hauptmotiv ist der vom rechten Coverrand hineinragende 'Blaue Drachen' (Glaucus atlanticus, siehe hochgeladenes Beispielbild von Wissnetz)
- Schriftart von Autorenname und Genre eher klar
- eigene Detailvorschläge zur Optimierung des Ergebnisses möglich bzw. erwünscht

```html
<!DOCTYPE html>
<html lang="de">
<head>
<meta charset="utf-8">
<title>Kaltgrund – Cover-Entwürfe</title>
<link rel="stylesheet" href="https://fonts.googleapis.com/css2?family=Oswald:wght@300;400&family=Kaushan+Script&family=Metal+Mania&display=swap">
<style>
  :root {
    --sheet: #c8c8c8;
    --ice-light: #f4fbfd;
    --ice-mid: #cfe8f1;
    --ice-deep: #9fcfe0;
    --creature-deep: #0d1f5c;
    --creature-mid: #2457a8;
    --creature-light: #7fb6e6;
    --ink: #0b0b0d;
    --band-blue: #10245a;
    --title-red: #d4161c;
    --title-orange: #e8691a;
    --title-gold: #f6b32a;
    --paper: #f2f2f2;
  }
  * { box-sizing: border-box; margin: 0; padding: 0; }
  html, body { width: 799px; height: 1200px; overflow: hidden; }
  body { background: var(--sheet); position: relative; }

  .cover {
    position: absolute;
    top: 334px;
    width: 332px;
    height: 532px;
    overflow: hidden;
  }
  .cover--script { left: 48px; }
  .cover--gothic { left: 423px; }

  .ice-field {
    position: absolute; inset: 0;
    background:
      radial-gradient(ellipse at 50% 20%, var(--ice-light) 0%, transparent 55%),
      radial-gradient(ellipse at 70% 75%, var(--ice-deep) 0%, transparent 60%),
      linear-gradient(160deg, var(--ice-mid), var(--ice-light) 45%, var(--ice-mid));
  }
  .sea-dragon {
    position: absolute;
    background: radial-gradient(ellipse at 50% 50%, var(--creature-deep) 0%, var(--creature-mid) 35%, var(--creature-light) 60%, transparent 72%);
  }
  .cover--script .sea-dragon { left: 10px; top: 220px; width: 330px; height: 320px; }
  .cover--gothic .sea-dragon { left: 60px; top: 200px; width: 300px; height: 340px; }

  .author-band {
    position: absolute;
  }
  .cover--script .author-band {
    left: 28px; top: 22px; width: 290px; height: 62px;
    background: var(--ink);
    transform: rotate(-2deg);
  }
  .cover--gothic .author-band {
    left: 40px; top: 30px; width: 280px; height: 66px;
    background: var(--band-blue);
    transform: rotate(-10deg);
  }

  .author {
    position: absolute;
    font-family: "Oswald", sans-serif;
    font-weight: 300;
    text-transform: uppercase;
    white-space: nowrap;
    letter-spacing: 1px;
  }
  .cover--script .author {
    left: 58px; top: 30px;
    font-size: 32px; line-height: 44px;
    color: var(--paper);
  }
  .cover--gothic .author {
    left: 52px; top: 42px;
    font-size: 38px; line-height: 48px;
    color: var(--paper);
    transform: rotate(-10deg);
    transform-origin: left top;
  }

  .title {
    position: absolute;
    white-space: nowrap;
  }
  .cover--script .title {
    left: 18px; top: 100px;
    font-family: "Kaushan Script", cursive;
    font-size: 72px; line-height: 90px;
    color: var(--ink);
    text-shadow: 3px 2px 0 var(--title-red);
    transform: rotate(-14deg);
    transform-origin: left center;
  }
  .cover--gothic .title {
    left: 18px; top: 150px;
    font-family: "Metal Mania", cursive;
    font-size: 66px; line-height: 80px;
    color: var(--title-orange);
    background: linear-gradient(180deg, var(--title-gold), var(--title-orange) 55%, #b8360e);
    -webkit-background-clip: text;
    background-clip: text;
    -webkit-text-fill-color: transparent;
    transform: rotate(-14deg);
    transform-origin: left center;
  }

  .genre-band {
    position: absolute;
    left: -10px; top: 420px; width: 190px; height: 72px;
    background: var(--ink);
    transform: rotate(-12deg);
  }
  .genre {
    position: absolute;
    font-family: "Oswald", sans-serif;
    font-weight: 400;
    text-transform: uppercase;
    white-space: nowrap;
  }
  .cover--script .genre {
    left: 44px; top: 450px;
    font-size: 46px; line-height: 56px;
    color: var(--ink);
    transform: scaleX(0.8);
    transform-origin: left top;
  }
  .cover--gothic .genre {
    left: 34px; top: 428px;
    font-weight: 300;
    font-size: 44px; line-height: 56px;
    color: var(--paper);
    transform: rotate(-12deg);
  }
</style>
</head>
<body>
  <section class="cover cover--script" aria-label="Cover-Entwurf mit Pinselschrift">
    <div class="ice-field" role="img" aria-label="Helle Eisfläche mit feinen Rissen"></div>
    <div class="sea-dragon" role="img" aria-label="Blauer Drache (Glaucus atlanticus) ragt von rechts ins Bild"></div>
    <div class="author-band"></div>
    <p class="author">Konrad Velten</p>
    <h1 class="title">Kaltgrund</h1>
    <p class="genre">Thriller</p>
  </section>

  <section class="cover cover--gothic" aria-label="Cover-Entwurf mit gezackter Schrift">
    <div class="ice-field" role="img" aria-label="Helle Eisfläche mit feinen Rissen"></div>
    <div class="sea-dragon" role="img" aria-label="Blauer Drache (Glaucus atlanticus) ragt von rechts ins Bild"></div>
    <div class="author-band"></div>
    <p class="author">Konrad Velten</p>
    <h1 class="title">KALTGRUND</h1>
    <div class="genre-band"></div>
    <p class="genre">Thriller</p>
  </section>
</body>
</html>
```